SEO Friendly Web Design Needed for Leading Software Company

Founded in 1986, TRBW is the market leader for innovative software solutions for the heavy civil construction industry. Our suite of products, including the bestsellers GroundQuote® and SiteTrack®, are used by more than 40,000 workers every day to improve their proficiency at estimating, job management, resource management, safety and equipment maintenance. TRBW also offers new mobile applications and cloud computing services so companies can work on a wide array of devices including laptops, tablets and smartphones.

In addition to high quality software, TRBW is best known for providing world-class customer service, and for its friendly, employee-ownership culture. We offer a full range of professional support options to help customers maximize their software investment including implementation planning, training and INSTANT 24/7 phone support.

Goals, objectives and target audience

The goal of our new layout and design will be to increase conversions, enhance user experience and enhance our SERP rankings.

Our objectives are as follows:
1. Clean and well laid out home page. White space is OK.
2. CTAs in strategic locations throughout to drive conversions and MQLs
3. SEO rich content with appropriate layout to meet our SEO requirements
4. 2 Master Design Templates – Home & Internal
5. Custom Design elements for individual modules

Target Audience:
- Heavy / Civil Construction Industry
- C Level executives or persons in leadership roles who utilize our software
- MEN in the construction industry.

Requirements
Should not have
• Feminine design - our industry is largely male construction workers.
Don't use script or goofy fonts
Don't change the logo, or put it in an image where it is not easily viewable.

```html
<!DOCTYPE html>
<html lang="en">
<head>
<meta charset="utf-8">
<title>TRBW – Construction Estimating Software</title>
<link rel="stylesheet" href="https://fonts.googleapis.com/css2?family=Roboto:wght@300;400;500;700&display=swap">
<style>
:root{
  --green:#27a844;
  --green-dark:#1f8c38;
  --orange:#f08a1c;
  --ink:#222;
  --text:#444;
  --muted:#888;
  --line:#dcdcdc;
  --side:#ececec;
  --topbar:#3a3a3a;
  --footer:#1e1e1c;
  --btn-grey:#7d7d7d;
}
*{box-sizing:border-box;margin:0;padding:0}
html,body{width:1200px;height:3648px;overflow:hidden}
body{position:relative;background:#fff;font-family:'Roboto',Arial,sans-serif;color:var(--text)}
a{color:inherit;text-decoration:none}
ul{list-style:none}

/* top bar */
.topbar{position:absolute;top:0;left:0;width:1200px;height:20px;background:var(--topbar);font-size:11px;color:var(--orange);display:flex;justify-content:space-between;align-items:center;padding:0 95px}
.topbar .links a{margin-right:14px}
.topbar .contact{display:flex;gap:14px;align-items:center}
.topbar .phone{font-weight:700;font-size:13px;display:flex;gap:6px;align-items:center}

/* header */
.header{position:absolute;top:20px;left:0;width:1200px;height:100px;border-bottom:1px solid var(--line);display:flex;align-items:center;justify-content:space-between;padding:0 92px 0 95px}
.brand{display:flex;align-items:center;gap:10px;font-size:40px;font-weight:700;color:var(--green);letter-spacing:1px}
.brand .mark{width:34px;height:34px;background:var(--green)}
.nav{display:flex;gap:30px;font-size:18px;color:#777}
.nav .active{color:var(--orange)}

/* sidebar */
.sidebar{position:absolute;top:190px;left:95px;width:243px;height:1032px;background:var(--side)}
.side-head{background:var(--green);color:#fff;font-size:28px;font-weight:400;height:60px;line-height:60px;padding-left:18px;border-bottom:4px solid #bfe8c9}
.side-menu li{height:37px;line-height:37px;border-bottom:1px solid #d6d6d6;font-size:12.5px;color:#555;padding-left:18px}
.side-menu li.current{background:#fff;color:var(--orange);font-weight:500}
.side-title{color:var(--green);font-size:28px;padding:30px 18px 10px;border-bottom:3px solid var(--green);margin:0 0 10px}
.side-list li{font-size:12.5px;color:#444;padding:9px 18px 9px 30px;border-bottom:1px solid #d6d6d6;position:relative;line-height:1.3}
.side-list li::before{content:"";position:absolute;left:18px;top:15px;width:4px;height:4px;background:#666}
.side-text{font-size:12.5px;line-height:1.55;color:#444;padding:6px 18px}

/* main */
.main{position:absolute;left:357px;width:751px}
h1.page-title{font-size:46px;font-weight:700;color:var(--ink);letter-spacing:-.5px;line-height:1.1}
.intro{font-size:16.5px;line-height:1.35;color:#333;margin-top:10px}
.benefit h2{font-size:38px;font-weight:400;color:var(--orange);letter-spacing:-.5px;line-height:1.1}

.row{display:flex;justify-content:space-between;align-items:flex-start}
.media{width:377px;height:270px;position:relative;box-shadow:0 2px 8px rgba(0,0,0,.18);padding:6px;background:#fff}
.media .fill{width:100%;height:100%}
.fill.excavator{background:linear-gradient(160deg,#6d8fb3 0%,#9db4c8 35%,#c9a35a 60%,#5b4a32 100%)}
.fill.helmet{background:linear-gradient(170deg,#f7f7f7 0%,#ececec 30%,#f19b2c 55%,#c9c9c9 80%,#9a9a9a 100%)}
.play{position:absolute;left:50%;top:45%;transform:translate(-50%,-50%)}
.testimonial{position:absolute;left:50%;bottom:6px;transform:translateX(-50%);background:#fff;color:var(--orange);font-size:11.5px;padding:6px 22px}

.checks{width:350px}
.checks li{font-size:13.5px;line-height:1.3;color:#333;padding:8px 0 10px 22px;border-bottom:1px solid var(--line);position:relative;min-height:62px}
.checks li svg{position:absolute;left:0;top:10px}
.ctas{display:flex;gap:8px;margin-top:12px}
.btn{font-size:11.5px;color:#fff;height:24px;line-height:24px;padding:0 18px 0 10px;clip-path:polygon(0 0,calc(100% - 8px) 0,100% 50%,calc(100% - 8px) 100%,0 100%)}
.btn.go{background:var(--green)}
.btn.warm{background:var(--orange)}
.btn.quiet{background:var(--btn-grey)}

.divider{position:absolute;left:357px;top:642px;width:751px;height:1px;background:linear-gradient(90deg,transparent,#ccc 30%,#ccc 70%,transparent)}
.divider span{position:absolute;left:50%;top:-9px;width:18px;height:18px;margin-left:-9px;border-radius:50%;background:#333;border:3px solid #fff;box-shadow:0 0 0 1px #ccc}

.to-top{position:absolute;left:1130px;top:1058px;width:70px;height:42px;background:var(--green);color:#fff;font-size:10px;font-weight:700;line-height:1.1;padding:9px 0 0 16px;clip-path:polygon(8px 0,100% 0,100% 100%,8px 100%,0 50%)}

/* footer */
.footer{position:absolute;top:3100px;left:0;width:1200px;height:492px;background:var(--footer);overflow:hidden}
.footer-photo{position:absolute;inset:0;background:radial-gradient(ellipse at 45% 35%,#5a4f36 0%,#2f2b22 45%,#181816 100%)}
.footer-logo{position:absolute;left:565px;top:0;width:70px;height:46px;background:#fff;color:var(--green);font-weight:700;font-size:18px;text-align:center;line-height:46px}
.footer-cols{position:absolute;top:95px;left:95px;display:flex}
.fcol{width:210px}
.fcol h4{color:var(--orange);font-size:16px;font-weight:500;padding-bottom:8px;border-bottom:1px solid rgba(255,255,255,.25);width:155px;margin-bottom:6px}
.fcol li{font-size:12px;color:#ddd;height:24px;line-height:24px;padding-left:12px;position:relative}
.fcol li::before{content:"›";position:absolute;left:2px;color:#bbb}
.fcol li.hl{background:#fff;color:var(--orange);width:155px}
.fcol h4.next{margin-top:20px}
.contact-list li{padding-left:18px;display:flex;gap:10px}
.contact-list li::before{content:none}
.contact-list .k{width:50px}
.contact-list svg{position:absolute;left:0;top:6px}
.contact-list li.addr{height:auto;line-height:1.3;padding-top:6px}
.social{display:flex;gap:8px;margin-top:12px}
.social span{width:26px;height:26px;border-radius:50%;border:1.5px solid #ddd}
.social span.on{background:#2aa3d8;border-color:#2aa3d8}
.follow{font-size:11px;color:#2aa3d8;margin:4px 0 0 32px}

.bottombar{position:absolute;top:3592px;left:0;width:1200px;height:56px;background:var(--green);color:#e8ffe8;font-size:12px;line-height:56px;padding-left:95px}
.bottombar a{margin-left:16px}
</style>
</head>
<body>

<div class="topbar">
  <div class="links"><a href="#">Tools</a><a href="#">News</a><a href="#">Blogs</a></div>
  <div class="contact">
    <a href="#">Contact Us</a><a href="#">Sales</a>
    <span class="phone"><svg width="11" height="11" viewBox="0 0 24 24"><path fill="#f08a1c" d="M6.6 10.8a15 15 0 0 0 6.6 6.6l2.2-2.2c.3-.3.7-.4 1-.2 1.1.4 2.3.6 3.6.6.6 0 1 .4 1 1V20c0 .6-.4 1-1 1A17 17 0 0 1 3 4c0-.6.4-1 1-1h3.5c.6 0 1 .4 1 1 0 1.3.2 2.5.6 3.6.1.3 0 .7-.2 1z"/></svg>1800 555 0100</span>
  </div>
</div>

<header class="header">
  <div class="brand"><span class="mark"></span>TRBW</div>
  <nav class="nav">
    <a class="active" href="#">Software</a><a href="#">Services</a><a href="#">Pricing</a><a href="#">Careers</a><a href="#">Events</a><a href="#">About Us</a>
  </nav>
</header>

<aside class="sidebar">
  <div class="side-head">Software</div>
  <ul class="side-menu">
    <li class="current">+ Estimating &amp; Bidding</li>
    <li>+ Jobs Management</li>
    <li>+ Dispatching &amp; Scheduling</li>
    <li>+ Safety Management</li>
    <li>+ Equipment Maintenance</li>
    <li>+ Fuel Tracking</li>
    <li>+ Mobile Apps</li>
  </ul>
  <h3 class="side-title">Services</h3>
  <ul class="side-list">
    <li>Lorem ipsum dolor sit amet, consectetur sed.</li>
    <li>Dolor sit amet, consectetur sed eiusmod incididunt</li>
    <li>Lorem ipsum dolor sit amet, consectetur &amp; sed eiusmod incididunt</li>
    <li>Consectetur sed eiusmod incididunt</li>
  </ul>
  <h3 class="side-title">Pricing</h3>
  <p class="side-text">Lorem ipsum dolor sit amet, consectetur sed. Dolor sit amet, consectetur ed eiusmod incididunt Lorem ipsum dolor sit amet, consectetur sed eiusmod incididunt Consectetur sed eiusmod incididunt</p>
</aside>

<main>
  <section class="main hero" style="top:185px">
    <h1 class="page-title">Construction Estimating Software</h1>
    <p class="intro">Lorem ipsum dolor sit amet, consectetur adipiscing elit, sed do eiusmod tempor incididunt ut labore et dolore magna aliqua.</p>
    <div class="row" style="margin-top:18px">
      <div class="media">
        <div class="fill excavator" role="img" aria-label="Video still: construction worker in a hard hat in front of an excavator"></div>
        <svg class="play" width="60" height="60" viewBox="0 0 60 60"><circle cx="30" cy="30" r="28" fill="rgba(255,255,255,.85)"/><path d="M24 18l18 12-18 12z" fill="#777"/></svg>
        <a class="testimonial" href="#">Customer Testimonial Link</a>
      </div>
      <div class="checks">
        <ul>
          <li><svg width="12" height="12" viewBox="0 0 12 12"><path d="M1 6l3 4 7-9" fill="none" stroke="#333" stroke-width="1.6"/></svg>Lorem ipsum dolor sit amet, consectetur sed eiusmod incididunt</li>
          <li><svg width="12" height="12" viewBox="0 0 12 12"><path d="M1 6l3 4 7-9" fill="none" stroke="#333" stroke-width="1.6"/></svg>Lorem ipsum dolor sit amet, consectetur adipiscing eiusmod tempor</li>
          <li><svg width="12" height="12" viewBox="0 0 12 12"><path d="M1 6l3 4 7-9" fill="none" stroke="#333" stroke-width="1.6"/></svg>Amet, consectetur adipiscing elit, lorem ipsum dolor sit amet</li>
          <li><svg width="12" height="12" viewBox="0 0 12 12"><path d="M1 6l3 4 7-9" fill="none" stroke="#333" stroke-width="1.6"/></svg>Consectetur sed eiusmod incididunt lorem ipsum consectetur sed</li>
        </ul>
        <div class="ctas"><a class="btn go" href="#">Contact Sales</a><a class="btn warm" href="#">Calculate ROI</a><a class="btn warm" href="#">Demo</a></div>
      </div>
    </div>
  </section>

  <div class="divider"><span></span></div>

  <!-- Benefit 1 -->
  <section class="main benefit" style="top:680px">
    <h2>Software Benefits # 1</h2>
    <p class="intro">Lorem ipsum dolor sit amet, consectetur adipiscing elit, sed do eiusmod tempor incididunt ut labore et dolore magna aliqua.</p>
    <div class="row" style="margin-top:22px">
      <div class="checks">
        <ul>
          <li><svg width="12" height="12" viewBox="0 0 12 12"><path d="M1 6l3 4 7-9" fill="none" stroke="#333" stroke-width="1.6"/></svg>Lorem ipsum dolor sit amet, consectetur sed eiusmod incididunt</li>
          <li><svg width="12" height="12" viewBox="0 0 12 12"><path d="M1 6l3 4 7-9" fill="none" stroke="#333" stroke-width="1.6"/></svg>Lorem ipsum dolor sit amet, consectetur adipiscing eiusmod tempor</li>
          <li><svg width="12" height="12" viewBox="0 0 12 12"><path d="M1 6l3 4 7-9" fill="none" stroke="#333" stroke-width="1.6"/></svg>Amet, consectetur adipiscing elit, lorem ipsum dolor sit amet</li>
          <li><svg width="12" height="12" viewBox="0 0 12 12"><path d="M1 6l3 4 7-9" fill="none" stroke="#333" stroke-width="1.6"/></svg>Consectetur sed eiusmod incididunt lorem ipsum consectetur sed</li>
        </ul>
        <div class="ctas"><a class="btn go" href="#">Contact Sales</a><a class="btn quiet" href="#">Calculate ROI</a><a class="btn quiet" href="#">Demo</a></div>
      </div>
      <div class="media">
        <div class="fill helmet" role="img" aria-label="Video still: orange hard hat resting on construction blueprints"></div>
        <svg class="play" width="60" height="60" viewBox="0 0 60 60"><circle cx="30" cy="30" r="28" fill="rgba(255,255,255,.85)"/><path d="M24 18l18 12-18 12z" fill="#777"/></svg>
        <a class="testimonial" href="#">Customer Testimonial Link</a>
      </div>
    </div>
  </section>

  <!-- Benefit 2 -->
  <section class="main benefit" style="top:1160px">
    <h2>Software Benefits # 2</h2>
    <p class="intro">Lorem ipsum dolor sit amet, consectetur adipiscing elit, sed do eiusmod tempor incididunt ut labore et dolore magna aliqua.</p>
    <div class="row" style="margin-top:22px">
      <div class="media">
        <div class="fill excavator" role="img" aria-label="Video still: excavator bucket digging earth under a blue sky"></div>
        <svg class="play" width="60" height="60" viewBox="0 0 60 60"><circle cx="30" cy="30" r="28" fill="rgba(255,255,255,.85)"/><path d="M24 18l18 12-18 12z" fill="#777"/></svg>
        <a class="testimonial" href="#">Customer Testimonial Link</a>
      </div>
      <div class="checks">
        <ul>
          <li><svg width="12" height="12" viewBox="0 0 12 12"><path d="M1 6l3 4 7-9" fill="none" stroke="#333" stroke-width="1.6"/></svg>Lorem ipsum dolor sit amet, consectetur sed eiusmod incididunt</li>
          <li><svg width="12" height="12" viewBox="0 0 12 12"><path d="M1 6l3 4 7-9" fill="none" stroke="#333" stroke-width="1.6"/></svg>Lorem ipsum dolor sit amet, consectetur adipiscing eiusmod tempor</li>
          <li><svg width="12" height="12" viewBox="0 0 12 12"><path d="M1 6l3 4 7-9" fill="none" stroke="#333" stroke-width="1.6"/></svg>Amet, consectetur adipiscing elit, lorem ipsum dolor sit amet</li>
          <li><svg width="12" height="12" viewBox="0 0 12 12"><path d="M1 6l3 4 7-9" fill="none" stroke="#333" stroke-width="1.6"/></svg>Consectetur sed eiusmod incididunt lorem ipsum consectetur sed</li>
        </ul>
        <div class="ctas"><a class="btn go" href="#">Contact Sales</a><a class="btn quiet" href="#">Calculate ROI</a><a class="btn quiet" href="#">Demo</a></div>
      </div>
    </div>
  </section>

  <!-- Benefit 3 -->
  <section class="main benefit" style="top:1635px">
    <h2>Software Benefits # 3</h2>
    <p class="intro">Lorem ipsum dolor sit amet, consectetur adipiscing elit, sed do eiusmod tempor incididunt ut labore et dolore magna aliqua.</p>
    <div class="row" style="margin-top:22px">
      <div class="checks">
        <ul>
          <li><svg width="12" height="12" viewBox="0 0 12 12"><path d="M1 6l3 4 7-9" fill="none" stroke="#333" stroke-width="1.6"/></svg>Lorem ipsum dolor sit amet, consectetur sed eiusmod incididunt</li>
          <li><svg width="12" height="12" viewBox="0 0 12 12"><path d="M1 6l3 4 7-9" fill="none" stroke="#333" stroke-width="1.6"/></svg>Lorem ipsum dolor sit amet, consectetur adipiscing eiusmod tempor</li>
          <li><svg width="12" height="12" viewBox="0 0 12 12"><path d="M1 6l3 4 7-9" fill="none" stroke="#333" stroke-width="1.6"/></svg>Amet, consectetur adipiscing elit, lorem ipsum dolor sit amet</li>
          <li><svg width="12" height="12" viewBox="0 0 12 12"><path d="M1 6l3 4 7-9" fill="none" stroke="#333" stroke-width="1.6"/></svg>Consectetur sed eiusmod incididunt lorem ipsum consectetur sed</li>
        </ul>
        <div class="ctas"><a class="btn go" href="#">Contact Sales</a><a class="btn quiet" href="#">Calculate ROI</a><a class="btn quiet" href="#">Demo</a></div>
      </div>
      <div class="media">
        <div class="fill helmet" role="img" aria-label="Video still: orange hard hat resting on construction blueprints"></div>
        <svg class="play" width="60" height="60" viewBox="0 0 60 60"><circle cx="30" cy="30" r="28" fill="rgba(255,255,255,.85)"/><path d="M24 18l18 12-18 12z" fill="#777"/></svg>
        <a class="testimonial" href="#">Customer Testimonial Link</a>
      </div>
    </div>
  </section>

  <!-- Benefit 4 -->
  <section class="main benefit" style="top:2098px">
    <h2>Software Benefits # 4</h2>
    <p class="intro">Lorem ipsum dolor sit amet, consectetur adipiscing elit, sed do eiusmod tempor incididunt ut labore et dolore magna aliqua.</p>
    <div class="row" style="margin-top:22px">
      <div class="media">
        <div class="fill excavator" role="img" aria-label="Video still: construction worker in a hard hat in front of an excavator"></div>
        <svg class="play" width="60" height="60" viewBox="0 0 60 60"><circle cx="30" cy="30" r="28" fill="rgba(255,255,255,.85)"/><path d="M24 18l18 12-18 12z" fill="#777"/></svg>
        <a class="testimonial" href="#">Customer Testimonial Link</a>
      </div>
      <div class="checks">
        <ul>
          <li><svg width="12" height="12" viewBox="0 0 12 12"><path d="M1 6l3 4 7-9" fill="none" stroke="#333" stroke-width="1.6"/></svg>Lorem ipsum dolor sit amet, consectetur sed eiusmod incididunt</li>
          <li><svg width="12" height="12" viewBox="0 0 12 12"><path d="M1 6l3 4 7-9" fill="none" stroke="#333" stroke-width="1.6"/></svg>Lorem ipsum dolor sit amet, consectetur adipiscing eiusmod tempor</li>
          <li><svg width="12" height="12" viewBox="0 0 12 12"><path d="M1 6l3 4 7-9" fill="none" stroke="#333" stroke-width="1.6"/></svg>Amet, consectetur adipiscing elit, lorem ipsum dolor sit amet</li>
          <li><svg width="12" height="12" viewBox="0 0 12 12"><path d="M1 6l3 4 7-9" fill="none" stroke="#333" stroke-width="1.6"/></svg>Consectetur sed eiusmod incididunt lorem ipsum consectetur sed</li>
        </ul>
        <div class="ctas"><a class="btn go" href="#">Contact Sales</a><a class="btn quiet" href="#">Calculate ROI</a><a class="btn quiet" href="#">Demo</a></div>
      </div>
    </div>
  </section>

  <!-- Benefit 5 -->
  <section class="main benefit" style="top:2570px">
    <h2>Software Benefits # 5</h2>
    <p class="intro">Lorem ipsum dolor sit amet, consectetur adipiscing elit, sed do eiusmod tempor incididunt ut labore et dolore magna aliqua.</p>
    <div class="row" style="margin-top:22px">
      <div class="checks">
        <ul>
          <li><svg width="12" height="12" viewBox="0 0 12 12"><path d="M1 6l3 4 7-9" fill="none" stroke="#333" stroke-width="1.6"/></svg>Lorem ipsum dolor sit amet, consectetur sed eiusmod incididunt</li>
          <li><svg width="12" height="12" viewBox="0 0 12 12"><path d="M1 6l3 4 7-9" fill="none" stroke="#333" stroke-width="1.6"/></svg>Lorem ipsum dolor sit amet, consectetur adipiscing eiusmod tempor</li>
          <li><svg width="12" height="12" viewBox="0 0 12 12"><path d="M1 6l3 4 7-9" fill="none" stroke="#333" stroke-width="1.6"/></svg>Amet, consectetur adipiscing elit, lorem ipsum dolor sit amet</li>
          <li><svg width="12" height="12" viewBox="0 0 12 12"><path d="M1 6l3 4 7-9" fill="none" stroke="#333" stroke-width="1.6"/></svg>Consectetur sed eiusmod incididunt lorem ipsum consectetur sed</li>
        </ul>
        <div class="ctas"><a class="btn go" href="#">Contact Sales</a><a class="btn quiet" href="#">Calculate ROI</a><a class="btn quiet" href="#">Demo</a></div>
      </div>
      <div class="media">
        <div class="fill excavator" role="img" aria-label="Video still: excavator bucket digging earth under a blue sky"></div>
        <svg class="play" width="60" height="60" viewBox="0 0 60 60"><circle cx="30" cy="30" r="28" fill="rgba(255,255,255,.85)"/><path d="M24 18l18 12-18 12z" fill="#777"/></svg>
        <a class="testimonial" href="#">Customer Testimonial Link</a>
      </div>
    </div>
  </section>
</main>

<a class="to-top" href="#">BACK<br>TO TOP</a>

<footer class="footer">
  <div class="footer-photo" role="img" aria-label="Blurred background photo of heavy machinery on a construction site"></div>
  <div class="footer-logo">TRBW</div>
  <div class="footer-cols">
    <div class="fcol">
      <h4>Softwares</h4>
      <ul>
        <li>GroundQuote</li><li class="hl">SiteTrack</li><li>Safety Application</li><li>The Router</li><li>GPS</li><li>Fleet 360</li><li>FuelLog Plus</li><li>quotearchive.example</li><li>Mobile Apps</li><li>Mobile Apps</li>
      </ul>
    </div>
    <div class="fcol">
      <h4>Serices</h4>
      <ul><li>Could Services</li><li>Custom Programming</li><li>Universities</li><li>Instant Support</li></ul>
      <h4 class="next">Training &amp; Events</h4>
      <ul><li>Training Options</li><li>Dummy Links Plz Ad</li></ul>
    </div>
    <div class="fcol">
      <h4>News</h4>
      <ul><li>Newsroom</li><li>Newsletter</li><li>Press Kit</li><li>Newsletter Subscription</li></ul>
      <h4 class="next">Careers</h4>
      <ul><li>Careers At TRBW</li><li>Careers In Construction</li></ul>
    </div>
    <div class="fcol">
      <h4>About Us</h4>
      <ul><li>About TRBW</li><li>TRBW Culture Blog</li><li>Our Clients</li><li>Contact/More Info</li><li>The TRBW Story</li><li>Map &amp; Directions</li><li>Stability</li><li>Why Choose TRBW</li></ul>
    </div>
    <div class="fcol">
      <h4>Contact Us</h4>
      <ul class="contact-list">
        <li><svg width="11" height="11" viewBox="0 0 24 24"><path fill="#ddd" d="M6.6 10.8a15 15 0 0 0 6.6 6.6l2.2-2.2c.3-.3.7-.4 1-.2 1.1.4 2.3.6 3.6.6.6 0 1 .4 1 1V20c0 .6-.4 1-1 1A17 17 0 0 1 3 4c0-.6.4-1 1-1h3.5c.6 0 1 .4 1 1 0 1.3.2 2.5.6 3.6.1.3 0 .7-.2 1z"/></svg><span class="k">Sales</span>800 - 555 - 0142</li>
        <li><svg width="11" height="11" viewBox="0 0 24 24"><path fill="#ddd" d="M6.6 10.8a15 15 0 0 0 6.6 6.6l2.2-2.2c.3-.3.7-.4 1-.2 1.1.4 2.3.6 3.6.6.6 0 1 .4 1 1V20c0 .6-.4 1-1 1A17 17 0 0 1 3 4c0-.6.4-1 1-1h3.5c.6 0 1 .4 1 1 0 1.3.2 2.5.6 3.6.1.3 0 .7-.2 1z"/></svg><span class="k">Support</span>800 - 555 - 0187</li>
        <li><svg width="11" height="11" viewBox="0 0 24 24"><path fill="#ddd" d="M2 5h20v14H2zm2 2v.5l8 5 8-5V7z"/></svg><span class="k">Email</span>info@trbw.example</li>
        <li class="addr"><svg width="11" height="14" viewBox="0 0 24 30"><path fill="#ddd" d="M12 0a10 10 0 0 0-10 10c0 8 10 20 10 20s10-12 10-20A10 10 0 0 0 12 0zm0 14a4 4 0 1 1 0-8 4 4 0 0 1 0 8z"/></svg><span>4400 Quarry Road,<br>Stone Ridge, TX 77000</span></li>
      </ul>
      <h4 class="next">Social Media</h4>
      <div class="social"><span></span><span class="on"></span><span></span><span></span><span></span></div>
      <p class="follow">Follow</p>
    </div>
  </div>
</footer>

<div class="bottombar">All Right Reserved © Copyright with www.trbw.example - 2013<a href="#">Terms</a><a href="#">Privacy Policy</a></div>

</body>
</html>
```